Morlavik APP redesign and color change

I am looking for a new design for my app. Please see the attached current design.

Currently, I have a functioning app but the colors and design are awful!
The logo is great but the rest of the app needs a refresh.
(Logo hi res not yet available but will upload soon.)
New colors or anything that is cutting edge.

Basically: It is a secure social media app within a school system where the teachers, students and parents can text, exchange photos, plan curriculum, etc.

I NEED ONLY landing page with a new look!
Looking for one distinct design for the landing page with new look.
The developer will apply this one design towards the rest of the pages/app screens.

Because part of the social media I need the feel and look of what is now the trend. Something that will attract and keep the client(s) interested. I am really leaving all the creative work to the designer and open to any suggestions.

Target Market(s)

Schools, community, teachers, students, colleges, sport teams

Industry/Entity Type

Non Profit

Font styles to use
Serif
Sans Serif

Colors

Designer to choose colors to be used in the design.

Requirements
Must have
• Sharp, trendy, millennial feel
Nice to have
• Up to designer
Should not have
• Up to designer

```html
<!DOCTYPE html>
<html lang="en">
<head>
<meta charset="utf-8">
<title>Morlavik – Sign In</title>
<link rel="stylesheet" href="https://fonts.googleapis.com/css2?family=Lato:wght@400;700&family=Roboto:wght@400&display=swap">
<style>
  :root {
    --photo-deep: #4a3a14;
    --photo-mid: #7a6a3e;
    --photo-light: #b7a879;
    --band-top: #3b4705;
    --band-bottom: #556300;
    --card-bg: rgba(250, 248, 242, 0.88);
    --label-gold: #b07a10;
    --button-gold: #b77c00;
    --ink: #2b2b2b;
    --rule: #6b6b6b;
    --white: #ffffff;
  }
  * { margin: 0; padding: 0; box-sizing: border-box; }
  html, body { width: 741px; height: 1200px; overflow: hidden; }
  body {
    position: relative;
    font-family: "Lato", sans-serif;
    background: var(--band-top);
  }
  .hero-photo {
    position: absolute; left: 0; top: 0; width: 741px; height: 1021px;
    background:
      radial-gradient(ellipse at 85% 55%, rgba(150,140,70,0.55), transparent 55%),
      radial-gradient(ellipse at 20% 90%, rgba(230,220,190,0.6), transparent 45%),
      linear-gradient(180deg, var(--photo-deep) 0%, var(--photo-mid) 45%, var(--photo-light) 100%);
  }
  .footer-band {
    position: absolute; left: 0; top: 1021px; width: 741px; height: 179px;
    background: linear-gradient(180deg, var(--band-top), var(--band-bottom));
  }
  .brand {
    position: absolute; left: 0; width: 741px; top: 445px;
    text-align: center;
    color: var(--white);
    font-family: "Lato", sans-serif;
    font-weight: 700;
    font-size: 34px;
    letter-spacing: 22px;
    padding-left: 22px;
  }
  .login-card {
    position: absolute; left: 93px; top: 653px; width: 555px; height: 317px;
    background: var(--card-bg);
  }
  .field-label {
    position: absolute; left: 61px;
    font-size: 17px; letter-spacing: 1.6px;
    color: var(--label-gold);
  }
  .label-username { top: 60px; }
  .label-password { top: 201px; }
  .field-value {
    position: absolute; left: 61px; top: 98px;
    font-family: "Roboto", sans-serif; font-size: 23px; color: var(--ink);
  }
  .field-rule {
    position: absolute; left: 61px; top: 165px; width: 433px; height: 1.5px;
    background: var(--rule);
  }
  .password-dots { position: absolute; left: 61px; top: 255px; }
  .submit-button {
    position: absolute; left: 93px; top: 970px; width: 555px; height: 106px;
    background: var(--button-gold);
    color: var(--white);
    font-size: 23px;
    display: flex; align-items: center; justify-content: space-between;
    padding: 0 66px 0 61px;
  }
  .register-link {
    position: absolute; left: 0; width: 741px; top: 1120px;
    text-align: center; color: var(--white); font-size: 18px;
  }
</style>
</head>
<body>
  <div class="hero-photo" role="img" aria-label="Blurred library bookshelves with a stack of books, coloured pencils, glasses and an open book on a desk"></div>
  <div class="footer-band"></div>

  <div class="brand">MORLAVIK</div>

  <form class="login-card">
    <div class="field-label label-username">USERNAME</div>
    <div class="field-value">jana@schoolmail.com</div>
    <div class="field-rule"></div>
    <div class="field-label label-password">PASSWORD</div>
    <svg class="password-dots" width="140" height="10" viewBox="0 0 140 10" aria-label="Hidden password">
      <g fill="#2b2b2b">
        <circle cx="5" cy="5" r="4.3"/><circle cx="22.5" cy="5" r="4.3"/>
        <circle cx="40" cy="5" r="4.3"/><circle cx="57.5" cy="5" r="4.3"/>
        <circle cx="75" cy="5" r="4.3"/><circle cx="92.5" cy="5" r="4.3"/>
        <circle cx="110" cy="5" r="4.3"/><circle cx="127.5" cy="5" r="4.3"/>
      </g>
    </svg>
  </form>

  <div class="submit-button">
    <span>Get Started</span>
    <svg width="13" height="18" viewBox="0 0 13 18" aria-hidden="true"><path d="M0 0 L13 9 L0 18 Z" fill="#111"/></svg>
  </div>

  <div class="register-link">Not registered? Create Account</div>
</body>
</html>
```